Heron Loan Partners Business Card

We need a business card design for our mortgage servicing company. In addition to servicing the loans of homeowners, we help homeowners with purchasing their homes and any mortgage refinancing. We would like to see designs that use the colors in the logo attached below (gold-ish yellow and navy blue), and any other design you deem fit! The design should communicate a simpler life with smart mortgages provided by Heron.

```html
<!DOCTYPE html>
<html lang="en">
<head>
<meta charset="UTF-8">
<title>Heron Mortgage Business Card</title>
<link href="https://fonts.googleapis.com/css2?family=Open+Sans:wght@400;600;700&display=swap" rel="stylesheet">
<style>
  :root {
    --backdrop: #333333;
    --navy: #272056;
    --gold: #e1b43f;
    --white: #ffffff;
    --ink: #1d1b2e;
  }
  * { box-sizing: border-box; margin: 0; padding: 0; }
  html, body { width: 1200px; height: 780px; overflow: hidden; }
  body {
    background: var(--backdrop);
    font-family: "Open Sans", Arial, sans-serif;
    display: flex;
    align-items: center;
    justify-content: center;
    gap: 40px;
  }
  .card {
    position: relative;
    width: 560px;
    height: 320px;
    overflow: hidden;
  }
  .card-back {
    background: var(--navy);
    display: flex;
    align-items: center;
    justify-content: center;
  }
  .brand {
    display: flex;
    align-items: center;
    gap: 14px;
    font-weight: 700;
    color: var(--gold);
  }
  .brand-mark {
    border-radius: 50%;
    background: var(--gold);
    flex: none;
  }
  .card-back .brand { font-size: 46px; }
  .card-back .brand-mark { width: 34px; height: 34px; }

  .card-front { background: var(--white); }
  .card-front .brand {
    position: absolute;
    left: 34px;
    top: 52px;
    font-size: 28px;
    gap: 10px;
  }
  .card-front .brand-mark { width: 20px; height: 20px; }

  .identity {
    position: absolute;
    right: 42px;
    top: 98px;
    text-align: right;
  }
  .person-name {
    font-size: 27px;
    font-weight: 700;
    line-height: 1.1;
    letter-spacing: 0.5px;
  }
  .first-name { color: var(--gold); }
  .last-name { color: var(--navy); }
  .job-title {
    font-size: 15px;
    font-weight: 600;
    color: var(--ink);
    margin-top: 2px;
  }
  .accent-bar {
    position: absolute;
    right: 14px;
    top: 92px;
    width: 12px;
    height: 68px;
    background: var(--gold);
  }
  .divider {
    position: absolute;
    left: 40px;
    right: 28px;
    top: 172px;
    height: 1.5px;
    background: var(--navy);
  }
  .address {
    position: absolute;
    right: 34px;
    top: 190px;
    text-align: right;
    font-size: 14px;
    line-height: 1.35;
    color: var(--ink);
  }
  .contacts {
    position: absolute;
    left: 40px;
    top: 196px;
    list-style: none;
    font-size: 14px;
    line-height: 1.45;
    color: var(--ink);
  }
  .contacts li { display: flex; align-items: center; gap: 8px; }
  .contacts svg { width: 13px; height: 13px; flex: none; }
  .footer-bands {
    position: absolute;
    left: 0;
    bottom: 0;
    width: 560px;
    height: 70px;
  }
</style>
</head>
<body>
  <section class="card card-back" aria-label="Card back">
    <div class="brand"><span class="brand-mark"></span>Heron Mortgage</div>
  </section>

  <section class="card card-front" aria-label="Card front">
    <div class="brand"><span class="brand-mark"></span>Heron Mortgage</div>

    <div class="identity">
      <p class="person-name"><span class="first-name">Lena</span> <span class="last-name">Varga</span></p>
      <p class="job-title">Managing Director</p>
    </div>
    <div class="accent-bar"></div>
    <div class="divider"></div>

    <address class="address" style="font-style:normal">
      1840 Lakeside Ave. Suite 300<br>Riverton, TX 75010
    </address>

    <ul class="contacts">
      <li>
        <svg viewBox="0 0 24 24"><path fill="#e1b43f" d="M6.6 10.8a15.1 15.1 0 0 0 6.6 6.6l2.2-2.2c.3-.3.7-.4 1-.2 1.1.4 2.3.6 3.6.6.6 0 1 .4 1 1V20c0 .6-.4 1-1 1A17 17 0 0 1 3 4c0-.6.4-1 1-1h3.5c.6 0 1 .4 1 1 0 1.3.2 2.5.6 3.6.1.3 0 .7-.2 1z"/></svg>
        (555) 214-0386
      </li>
      <li>
        <svg viewBox="0 0 24 24"><rect x="2" y="5" width="20" height="14" rx="1.5" fill="#e1b43f"/><path d="M3 6l9 7 9-7" fill="none" stroke="#fff" stroke-width="1.6"/></svg>
        info@heronloanpartners.com
      </li>
      <li>
        <svg viewBox="0 0 24 24"><circle cx="12" cy="12" r="10" fill="#e1b43f"/><path d="M2 12h20M12 2c3 3 3 17 0 20M12 2c-3 3-3 17 0 20" fill="none" stroke="#fff" stroke-width="1.4"/></svg>
        www.heronloanpartners.com
      </li>
    </ul>

    <svg class="footer-bands" viewBox="0 0 560 70" aria-hidden="true">
      <path fill="#e1b43f" d="M0 44 H398 L406 36 V42 L400 50 H0 Z"/>
      <path fill="#272056" d="M0 56 H404 L414 44 Q420 36 430 36 H560 V70 H0 Z"/>
    </svg>
  </section>
</body>
</html>
```